Exciting opportunity to create logo and a label for our natural health brand.

About us

We are a customer centric health supplement brand who believes in natural medicine and high quality ingredients. We take a holistic approach to healthcare, with an eastern philosophy. We believe in being partners with our customers in their health care journey and are invested in their well being.

Our brand philosophy and values are attached (see Vorna philosophy.png). Our personality traits are:

- Natural
- Fresh
- Modern
- Balanced (in a holistic sense)

Task breakdown

1. Design a fresh feeling logo for us
- We want it to represent our values and high quality ingredients. We would like the quality of the product to be reflected in the branding and have a high end feel.
- Logo text must include Vorna Health Sciences
- We want the Vorna to be the focus of the logo (see uploaded image Vorna logo example.png)
The logo does not have to follow this layout, but we just want the Vorna to stand out. Feel free to use your creative license on this!

2. Create an attractive label to go on the supplement bottle
- The designs need to be eye catching, give a sense of high end ingredients and natural products and tie in with the logo to give a joined up feel.
- We are selling our products online and need them to really stand out from the competition.
- See examples of labels and packaging we like (1 -7 label design).

The initial label we would like you to design would be for our product Calm Drift. It is a product that assists in the management of Anxiety and stress. The label will appear on the bottle that holds the capsules for this supplement, see uploaded files (Example plain bottles.png). The bottles may be white as the picture shows or dark blue recyclable plastic or dark brown glass . We don't have the exact dimensions of the bottle yet, but I will follow up with these.

The label needs to include the following things:
1. The logo
2. The name of the product
3. The product is to help with the relief of Anxiety and Stress
4. Number of capsules the bottle contains
5. The back of the label should have
i) The ingredients
ii) Dosage
iii) Directions of use

Please use placeholder text where needed.

We look forward to seeing your design. Thank you.

```html
<!DOCTYPE html>
<html lang="en">
<head>
<meta charset="UTF-8">
<title>Vorna Health Sciences – Calm Drift Label</title>
<link rel="stylesheet" href="https://fonts.googleapis.com/css2?family=Barlow:wght@400;500;600&display=swap">
<style>
  :root {
    --backdrop: #9f9fd4;
    --lavender: #a3a3e0;
    --lavender-band: #aeaee6;
    --label-white: #ffffff;
    --text-grey: #6b6b6b;
    --text-dark-grey: #5c5c5c;
    --botanical-green: #b7c79a;
    --botanical-grey: #e2e2e2;
  }
  * { margin: 0; padding: 0; box-sizing: border-box; }
  html, body {
    width: 1200px;
    height: 750px;
    overflow: hidden;
    background: var(--backdrop);
    font-family: "Barlow", sans-serif;
  }
  .canvas {
    position: relative;
    width: 1200px;
    height: 750px;
  }
  .label {
    position: absolute;
    left: 336px;
    top: 35px;
    width: 527px;
    height: 680px;
    background: var(--label-white);
    overflow: hidden;
  }
  .label-band {
    position: absolute;
    left: 0;
    width: 100%;
    height: 22px;
    background: var(--lavender-band);
  }
  .label-band--top { top: 0; }
  .label-band--bottom { bottom: 0; }
  .botanical-art {
    position: absolute;
    left: 250px;
    top: 110px;
    width: 277px;
    height: 548px;
    background:
      linear-gradient(100deg, rgba(226,226,226,0) 0%, rgba(226,226,226,0.55) 40%, rgba(183,199,154,0.55) 70%, rgba(226,226,226,0.5) 100%);
  }
  .brand {
    position: absolute;
    left: 0;
    top: 70px;
    width: 100%;
    text-align: center;
    color: var(--lavender);
    font-weight: 500;
  }
  .brand-name {
    display: block;
    font-size: 112px;
    line-height: 1;
    letter-spacing: 1px;
  }
  .brand-tagline {
    display: block;
    margin-top: 6px;
    font-size: 17px;
    letter-spacing: 6px;
    text-transform: uppercase;
  }
  .product-band {
    position: absolute;
    left: 0;
    top: 340px;
    width: 100%;
    height: 122px;
    background: var(--label-white);
    box-shadow: 0 -6px 10px rgba(0,0,0,0.08), 0 6px 10px rgba(0,0,0,0.08);
    text-align: center;
    padding-top: 24px;
  }
  .product-name {
    color: var(--lavender);
    font-weight: 600;
    font-size: 40px;
    line-height: 1.1;
  }
  .product-benefit {
    margin-top: 4px;
    color: var(--text-grey);
    font-weight: 500;
    font-size: 20px;
    letter-spacing: 0.5px;
  }
  .capsule-count {
    position: absolute;
    left: 0;
    top: 572px;
    width: 100%;
    text-align: center;
    color: var(--text-dark-grey);
  }
  .capsule-number {
    display: block;
    font-weight: 600;
    font-size: 36px;
    line-height: 1;
  }
  .capsule-unit {
    display: block;
    font-weight: 500;
    font-size: 25px;
    letter-spacing: 2px;
    line-height: 1.2;
  }
</style>
</head>
<body>
  <main class="canvas">
    <section class="label">
      <div class="label-band label-band--top"></div>
      <div class="botanical-art" role="img" aria-label="Line illustration of flowering herbs and leafy stems in soft green and grey"></div>
      <header class="brand">
        <span class="brand-name">vorna</span>
        <span class="brand-tagline">Health Sciences</span>
      </header>
      <div class="product-band">
        <h1 class="product-name">Calm Drift</h1>
        <p class="product-benefit">Reduce stress and anxiety naturally</p>
      </div>
      <div class="capsule-count">
        <span class="capsule-number">60</span>
        <span class="capsule-unit">capsules</span>
      </div>
      <div class="label-band label-band--bottom"></div>
    </section>
  </main>
</body>
</html>
```